Professional, modern and unique business card. We are looking to present a new look to our business cards however we don't want to divert too far away from original template. We want social media links and our 3 office addresses on the backside of the business cards. Please see attached business card templates for ideas.
Crestline Homes Color Code:
R: 7
G:63
B:86

Target Market(s)

Real Estate

Industry/Entity Type

Real Estate

Contact Information for Business Card

Follow the attached templates. In need of a more modern and unique touch but don't want to divert from the original theme or color.
Crestline Homes Color Code:
R: 7
G:63
B:86

Font styles to use
Serif

Requirements
Must have
• Crestline Homes logo, Crestline homes colors, social media links, 3 office addresses,
Nice to have
• information about Crestline Homes and QR codes. You can check out www.mycrestlinehomes.example

```html
<!DOCTYPE html>
<html lang="en">
<head>
<meta charset="utf-8">
<title>Crestline Homes business card</title>
<link rel="stylesheet" href="https://fonts.googleapis.com/css2?family=Work+Sans:wght@400;500&display=swap">
<style>
:root{
  --page:#e4e6e9;
  --brand-blue:#3a8fd1;
  --brand-deep:#2377bd;
  --ink:#2a2a2a;
  --white:#ffffff;
  --muted:#4a4a4a;
}
*{box-sizing:border-box;margin:0;padding:0}
html,body{width:1200px;height:715px;overflow:hidden}
body{background:var(--page);font-family:"Work Sans",Arial,sans-serif;position:relative}
.card{position:absolute;top:203px;width:540px;height:309px;overflow:hidden;box-shadow:0 6px 18px rgba(0,0,0,.18)}
.card--front{left:40px;background:var(--brand-blue);color:var(--white)}
.card--back{left:620px;background:var(--white);color:var(--ink)}

.wordmark{position:absolute;font-weight:500;letter-spacing:.14em;text-transform:uppercase;white-space:nowrap}
.card--front .wordmark{left:0;right:0;top:92px;text-align:center;font-size:34px;color:var(--white)}
.card--back .wordmark{left:40px;top:48px;font-size:26px;color:var(--ink)}

.offices{position:absolute;left:28px;right:28px;bottom:34px;display:flex;justify-content:space-between}
.office{font-size:12px;line-height:1.45;padding-left:12px;border-left:1px solid rgba(255,255,255,.8)}
.office:first-child{border-left:none;padding-left:0}

.rule{position:absolute;left:250px;right:0;top:106px;height:1px;background:var(--brand-blue)}
.agent{position:absolute;right:30px;top:116px;text-align:right}
.agent__name{font-size:21px;font-weight:500;letter-spacing:.04em;color:var(--brand-deep);text-transform:uppercase;line-height:26px}
.agent__title{font-size:12.5px;color:var(--muted);line-height:16px}
.agent__rule{position:absolute;right:30px;top:164px;width:190px;height:1px;background:var(--brand-deep)}

.contacts{position:absolute;left:40px;top:140px;list-style:none;font-size:12.5px;line-height:17px}
.contacts li{display:flex;align-items:center;gap:7px}
.contacts svg{width:10px;height:10px;flex:none}

.social{position:absolute;right:30px;top:172px;list-style:none;font-size:12px;line-height:15px;text-align:right;white-space:nowrap}
.social li{display:flex;justify-content:flex-end;align-items:center;gap:8px}
.social__dot{width:10px;height:10px;border-radius:2px;background:var(--brand-deep);flex:none}

.swoosh{position:absolute;left:0;bottom:0;width:540px;height:70px}
</style>
</head>
<body>

<section class="card card--front" aria-label="Card front">
  <div class="wordmark">Crestline Homes</div>
  <div class="offices">
    <p class="office">412 Harbor Ridge Rd<br>Maple Point, NY 10001</p>
    <p class="office">27 Orchard Lane<br>Fern Hollow, NY 10002</p>
    <p class="office">908 Summit Ave<br>Brookvale, NY 10003</p>
  </div>
</section>

<section class="card card--back" aria-label="Card back">
  <div class="wordmark">Crestline Homes</div>
  <div class="rule"></div>

  <div class="agent">
    <p class="agent__name">Daniel Harlow</p>
    <p class="agent__title">Associate Real Estate Broker</p>
  </div>
  <div class="agent__rule"></div>

  <ul class="contacts">
    <li><svg viewBox="0 0 10 10"><path d="M2 1h2l1 2-1.2 1a5 5 0 0 0 2.2 2.2L7 5l2 1v2a1 1 0 0 1-1 1A7 7 0 0 1 1 2a1 1 0 0 1 1-1z" fill="#2377bd"/></svg>555-014-2290</li>
    <li><svg viewBox="0 0 10 10"><rect x="2.5" y="0.5" width="5" height="9" rx="1" fill="none" stroke="#2377bd"/></svg>555-017-6634</li>
    <li><svg viewBox="0 0 10 10"><rect x="0.5" y="2" width="9" height="6" fill="none" stroke="#2377bd"/><path d="M.5 2 5 5.5 9.5 2" fill="none" stroke="#2377bd"/></svg>info@mycrestlinehomes.example</li>
    <li><svg viewBox="0 0 10 10"><circle cx="5" cy="5" r="4.5" fill="none" stroke="#2377bd"/><path d="M.5 5h9M5 .5v9" stroke="#2377bd"/></svg>www.mycrestlinehomes.example</li>
  </ul>

  <ul class="social">
    <li>CrestlineHomesNY<span class="social__dot"></span></li>
    <li>Info at Crestline Homes<span class="social__dot"></span></li>
    <li>@CrestlineHomes<span class="social__dot"></span></li>
    <li>Crestline Homes<span class="social__dot"></span></li>
    <li>Crestline Homes New York<span class="social__dot"></span></li>
    <li>@CrestlineHomesQ<span class="social__dot"></span></li>
  </ul>

  <svg class="swoosh" viewBox="0 0 540 70" aria-hidden="true">
    <path d="M0 16H220C262 16 280 58 322 58H540V70H0Z" fill="#3a8fd1"/>
    <path d="M0 10H212C222 10 228 13 234 17" fill="none" stroke="#2a2a2a" stroke-width="3"/>
  </svg>
</section>

</body>
</html>
```